Walk Beside The River

Business Card design

Target Market(s)

People who require support in the commnity

Industry/Entity Type

Mental Health Support

Contact Information for Business Card

Mental Health Support Rosalind Tavener walkbesidetheriver@mailcove.com.au 0481 637 092 PO Box 926 Riverbend Heights QLD 4571

Colors
6B429C
8869AF
B7A5CE
E3DAEB
F3F0F8

Requirements
Must have
• Logo & details listed above
Should not have
• No red or orange

```html
<!DOCTYPE html>
<html lang="en">
<head>
<meta charset="utf-8">
<title>Walk Beside The River — Business Card</title>
<link href="https://fonts.googleapis.com/css2?family=Lato:wght@400;700;900&family=Josefin+Sans:wght@400&display=swap" rel="stylesheet">
<style>
  :root {
    --stage: #2b2b2d;
    --front-light: #9a5fd2;
    --front-mid: #8a45c9;
    --front-deep: #7d3cc0;
    --back-purple: #6e44a0;
    --ink-light: #ffffff;
    --logo-cream: #f6f0d8;
    --sun-yellow: #f6ec1f;
  }
  * { margin: 0; padding: 0; box-sizing: border-box; }
  html, body {
    width: 1200px;
    height: 875px;
    overflow: hidden;
    background: var(--stage);
  }
  .canvas {
    position: relative;
    width: 1200px;
    height: 875px;
    display: flex;
    align-items: center;
    justify-content: center;
    gap: 50px;
  }
  .card {
    position: relative;
    width: 530px;
    height: 310px;
    border-radius: 22px;
    overflow: hidden;
  }

  /* Front side */
  .card-front {
    background:
      radial-gradient(ellipse at 75% 20%, var(--front-light) 0%, transparent 55%),
      radial-gradient(ellipse at 20% 85%, var(--front-light) 0%, transparent 50%),
      linear-gradient(135deg, var(--front-deep) 0%, var(--front-mid) 50%, var(--front-deep) 100%);
    display: flex;
    align-items: center;
    justify-content: center;
  }
  .brand {
    display: flex;
    align-items: center;
    gap: 14px;
  }
  .brand-dot {
    width: 30px;
    height: 30px;
    border-radius: 50%;
    background: var(--sun-yellow);
    flex-shrink: 0;
  }
  .brand-name {
    font-family: 'Josefin Sans', sans-serif;
    font-weight: 400;
    font-size: 22px;
    letter-spacing: 5px;
    text-transform: uppercase;
    color: var(--logo-cream);
  }

  /* Back side */
  .card-back {
    background: var(--back-purple);
    display: flex;
    align-items: center;
    padding: 0 30px;
    font-family: 'Lato', sans-serif;
    color: var(--ink-light);
  }
  .identity {
    flex-shrink: 0;
    text-align: right;
  }
  .person-name {
    font-weight: 900;
    font-size: 23px;
    letter-spacing: -0.3px;
    text-transform: uppercase;
    line-height: 1.05;
  }
  .person-role {
    font-weight: 400;
    font-size: 14px;
    margin-top: 2px;
  }
  .divider {
    width: 1.5px;
    height: 64px;
    background: var(--ink-light);
    margin: 0 16px;
    flex-shrink: 0;
  }
  .contacts {
    list-style: none;
    display: flex;
    flex-direction: column;
    gap: 3px;
  }
  .contact-item {
    display: flex;
    align-items: center;
    gap: 6px;
    font-size: 11px;
    white-space: nowrap;
  }
  .contact-item.phone { font-size: 17px; font-weight: 700; letter-spacing: 0.3px; }
  .contact-icon { width: 11px; height: 11px; flex-shrink: 0; fill: var(--ink-light); }
</style>
</head>
<body>
  <main class="canvas">
    <section class="card card-front" aria-label="Card front">
      <div class="brand">
        <span class="brand-dot"></span>
        <span class="brand-name">Walk Beside The River</span>
      </div>
    </section>

    <section class="card card-back" aria-label="Card back">
      <div class="identity">
        <h1 class="person-name">Rosalind Tavener</h1>
        <p class="person-role">Mental Health Support</p>
      </div>
      <span class="divider"></span>
      <ul class="contacts">
        <li class="contact-item phone">
          <svg class="contact-icon" viewBox="0 0 24 24" aria-hidden="true"><path d="M6.6 10.8a15.2 15.2 0 0 0 6.6 6.6l2.2-2.2a1 1 0 0 1 1-.25 11.4 11.4 0 0 0 3.6.57 1 1 0 0 1 1 1V20a1 1 0 0 1-1 1A17 17 0 0 1 3 4a1 1 0 0 1 1-1h3.5a1 1 0 0 1 1 1c0 1.25.2 2.45.57 3.57a1 1 0 0 1-.25 1z"/></svg>
          0481 637 092
        </li>
        <li class="contact-item">
          <svg class="contact-icon" viewBox="0 0 24 24" aria-hidden="true"><path d="M2 5h20v2l-10 7L2 7z"/><path d="M2 9l10 7 10-7v10H2z"/></svg>
          walkbesidetheriver@mailcove.com.au
        </li>
        <li class="contact-item">
          <svg class="contact-icon" viewBox="0 0 24 24" aria-hidden="true"><path d="M12 2a7 7 0 0 0-7 7c0 5.2 7 13 7 13s7-7.8 7-13a7 7 0 0 0-7-7zm0 9.5A2.5 2.5 0 1 1 12 6.5a2.5 2.5 0 0 1 0 5z"/></svg>
          PO Box 926 Riverbend Heights QLD 4571
        </li>
      </ul>
    </section>
  </main>
</body>
</html>
```